Supplement label and box design for Kivo/Relm Blend

we need the label and box design for our morning and nighttime supplement designed for entrepreneurs. They are energy and focus plus restorative sleep supplement stack. I have a full creative brief with video loom here: https://files.plinvora.com/doc/8kq2TzrW4mYpLx7cVn0aBdHs5eJgUf3RoiQ1tK6wZyE/view?mode=share

Target Market(s)

entreprenuers

Industry/Entity Type

Business Supplements

Requirements
Must have
• clean and sexy
Nice to have
• make sure it doesn't look like a pet supplement . . .this is for humans
Should not have
• don't use the full logo, just the text Quill Mark

```html
<!DOCTYPE html>
<html lang="en">
<head>
<meta charset="utf-8">
<title>Quill Mark — Kivo/Relm Blend Labels</title>
<link href="https://fonts.googleapis.com/css2?family=League+Spartan:wght@800&family=Oswald:wght@500;600&family=Poppins:wght@400;600;700&display=swap" rel="stylesheet">
<style>
  :root{
    --stage:#d9d9d9;
    --divider:#b4b4b4;
    --paper:#f7f7f7;
    --ink:#2b2b2b;
    --muted:#555;
    --kivo:#e8a835;
    --relm:#1f6fbf;
  }
  *{box-sizing:border-box;margin:0;padding:0}
  html,body{width:1200px;height:2700px;overflow:hidden;background:var(--stage)}
  .sheet{width:1200px;height:2700px;display:flex;flex-direction:column}
  .panel{position:relative;height:675px;background:var(--stage);border-bottom:22px solid var(--divider)}
  .panel:last-child{border-bottom:none}
  .label{
    position:absolute;left:300px;top:90px;width:600px;height:500px;
    background:var(--paper);overflow:hidden;border-radius:4px;
    box-shadow:0 12px 30px rgba(0,0,0,.12);
  }
  .label--kivo{--accent:var(--kivo)}
  .label--relm{--accent:var(--relm)}
  .band-top{position:absolute;left:0;top:0;width:100%;height:40px;background:var(--accent)}
  .band-note{
    position:absolute;left:0;width:100%;padding:0 20px;
    font:600 8px/1 "Poppins",sans-serif;letter-spacing:2.5px;white-space:nowrap;
    color:rgba(255,255,255,.85);display:flex;justify-content:space-between;text-transform:uppercase;
  }
  .band-top .band-note{top:16px}
  .brand-tab{
    position:absolute;left:200px;top:0;width:200px;height:60px;background:var(--accent);
    border-radius:0 0 18px 18px;display:flex;align-items:center;justify-content:center;
    font:700 22px/1 "Poppins",sans-serif;color:#fff;letter-spacing:.5px;text-transform:uppercase;
  }
  .product-name{
    position:absolute;left:0;top:104px;width:100%;text-align:center;
    font:800 112px/1 "League Spartan",sans-serif;color:var(--ink);letter-spacing:4px;
  }
  .benefits{position:absolute;left:120px;top:240px;width:360px;display:flex;justify-content:space-between}
  .benefit{width:100px;display:flex;flex-direction:column;align-items:center;gap:8px}
  .benefit svg{width:54px;height:54px}
  .benefit-caption{font:600 16px/1 "Oswald",sans-serif;color:var(--ink);text-transform:uppercase}
  .directions{position:absolute;left:40px;top:350px;width:160px}
  .directions h3{font:700 14px/1.2 "Poppins",sans-serif;color:var(--accent)}
  .directions p{font:400 10px/1.3 "Poppins",sans-serif;color:var(--muted)}
  .band-bottom{position:absolute;left:0;top:420px;width:100%;height:80px;background:var(--accent)}
  .band-bottom .band-note{top:62px}
  .servings-notch{
    position:absolute;left:210px;top:340px;width:180px;height:120px;background:var(--paper);
    border-radius:0 0 22px 22px;text-align:center;padding-top:4px;
  }
  .servings-count{font:600 62px/1 "Oswald",sans-serif;color:var(--accent)}
  .servings-word{font:500 24px/1.3 "Oswald",sans-serif;color:var(--ink);letter-spacing:3px}
  .band-fact{position:absolute;top:436px;font:500 26px/1 "Oswald",sans-serif;color:#fff;text-transform:uppercase}
  .band-fact--left{left:40px}
  .band-fact--right{right:40px}
  .icon-fill{fill:var(--accent)}
  .icon-line{fill:none;stroke:var(--accent);stroke-width:5;stroke-linecap:round;stroke-linejoin:round}
</style>
</head>
<body>
<main class="sheet">

  <!-- Kivo, variant 1 -->
  <section class="panel">
    <article class="label label--kivo">
      <div class="band-top"><div class="band-note"><span>Dietary supplement</span><span>Dietary supplement</span></div></div>
      <div class="brand-tab">Quill Mark</div>
      <h1 class="product-name">KIVO</h1>
      <div class="benefits">
        <div class="benefit"><svg viewBox="0 0 54 54"><path class="icon-fill" d="M31 2 12 30h13l-4 22 21-30H29z"/></svg><span class="benefit-caption">Energy</span></div>
        <div class="benefit"><svg viewBox="0 0 54 54"><path class="icon-line" d="M20 38c0-6-7-9-7-17a14 14 0 0 1 28 0c0 8-7 11-7 17z"/><path class="icon-line" d="M21 45h12M24 51h6"/></svg><span class="benefit-caption">Creativity</span></div>
        <div class="benefit"><svg viewBox="0 0 54 54"><circle class="icon-line" cx="27" cy="27" r="16"/><circle class="icon-fill" cx="27" cy="27" r="8"/><path class="icon-line" d="M27 3v8M27 43v8M3 27h8M43 27h8"/></svg><span class="benefit-caption">Focus</span></div>
      </div>
      <div class="directions"><h3>Direction:</h3><p>Take 3 capsules daily, in the morning or afternoon, with or without food.</p></div>
      <div class="band-bottom"><div class="band-note"><span>Dietary supplement</span><span>Dietary supplement</span><span>Dietary supplement</span></div></div>
      <div class="servings-notch"><div class="servings-count">30</div><div class="servings-word">SERVINGS</div></div>
      <span class="band-fact band-fact--left">90 Capsules</span>
      <span class="band-fact band-fact--right">3 Per Serving</span>
    </article>
  </section>

  <!-- Kivo, variant 2 -->
  <section class="panel">
    <article class="label label--kivo">
      <div class="band-top"><div class="band-note"><span>Dietary supplement</span><span>Dietary supplement</span></div></div>
      <div class="brand-tab">Quill Mark</div>
      <h1 class="product-name">KIVO</h1>
      <div class="benefits">
        <div class="benefit"><svg viewBox="0 0 54 54"><path class="icon-fill" d="M31 2 12 30h13l-4 22 21-30H29z"/></svg><span class="benefit-caption">Energy</span></div>
        <div class="benefit"><svg viewBox="0 0 54 54"><path class="icon-line" d="M20 38c0-6-7-9-7-17a14 14 0 0 1 28 0c0 8-7 11-7 17z"/><path class="icon-line" d="M21 45h12M24 51h6"/></svg><span class="benefit-caption">Creativity</span></div>
        <div class="benefit"><svg viewBox="0 0 54 54"><circle class="icon-line" cx="27" cy="27" r="16"/><circle class="icon-fill" cx="27" cy="27" r="8"/><path class="icon-line" d="M27 3v8M27 43v8M3 27h8M43 27h8"/></svg><span class="benefit-caption">Focus</span></div>
      </div>
      <div class="directions"><h3>Direction:</h3><p>Take 3 capsules daily, in the morning or afternoon, with or without food.</p></div>
      <div class="band-bottom"><div class="band-note"><span>Dietary supplement</span><span>Dietary supplement</span><span>Dietary supplement</span></div></div>
      <div class="servings-notch"><div class="servings-count">30</div><div class="servings-word">SERVINGS</div></div>
      <span class="band-fact band-fact--left">90 Capsules</span>
      <span class="band-fact band-fact--right">3 Per Serving</span>
    </article>
  </section>

  <!-- Relm, variant 1 -->
  <section class="panel">
    <article class="label label--relm">
      <div class="band-top"><div class="band-note"><span>Dietary supplement</span><span>Dietary supplement</span></div></div>
      <div class="brand-tab">Quill Mark</div>
      <h1 class="product-name">RELM</h1>
      <div class="benefits">
        <div class="benefit"><svg viewBox="0 0 54 54"><path class="icon-fill" d="M27 8c7 7 7 24 0 34-7-10-7-27 0-34z"/><path class="icon-fill" d="M6 22c10 0 18 9 19 20C14 42 7 33 6 22z"/><path class="icon-fill" d="M48 22c-10 0-18 9-19 20 11 0 18-9 19-20z"/><path class="icon-line" d="M10 47h34"/></svg><span class="benefit-caption">Relax</span></div>
        <div class="benefit"><svg viewBox="0 0 54 54"><path class="icon-line" d="M8 16l10 20h24"/><path class="icon-line" d="M18 36l-6 12M40 36l4 12M26 36l14-10"/></svg><span class="benefit-caption">Rest</span></div>
        <div class="benefit"><svg viewBox="0 0 54 54"><path class="icon-line" d="M44 20A18 18 0 0 0 12 16M10 34a18 18 0 0 0 32 4"/><path class="icon-fill" d="M30 14 20 30h7l-3 11 11-16h-7z"/></svg><span class="benefit-caption">Renew</span></div>
      </div>
      <div class="directions"><h3>Direction:</h3><p>Take 3 capsules daily, in the morning or afternoon, with or without food.</p></div>
      <div class="band-bottom"><div class="band-note"><span>Dietary supplement</span><span>Dietary supplement</span><span>Dietary supplement</span></div></div>
      <div class="servings-notch"><div class="servings-count">30</div><div class="servings-word">SERVINGS</div></div>
      <span class="band-fact band-fact--left">90 Capsules</span>
      <span class="band-fact band-fact--right">3 Per Serving</span>
    </article>
  </section>

  <!-- Relm, variant 2 -->
  <section class="panel">
    <article class="label label--relm">
      <div class="band-top"><div class="band-note"><span>Dietary supplement</span><span>Dietary supplement</span></div></div>
      <div class="brand-tab">Quill Mark</div>
      <h1 class="product-name">RELM</h1>
      <div class="benefits">
        <div class="benefit"><svg viewBox="0 0 54 54"><path class="icon-fill" d="M27 8c7 7 7 24 0 34-7-10-7-27 0-34z"/><path class="icon-fill" d="M6 22c10 0 18 9 19 20C14 42 7 33 6 22z"/><path class="icon-fill" d="M48 22c-10 0-18 9-19 20 11 0 18-9 19-20z"/><path class="icon-line" d="M10 47h34"/></svg><span class="benefit-caption">Relax</span></div>
        <div class="benefit"><svg viewBox="0 0 54 54"><path class="icon-line" d="M8 16l10 20h24"/><path class="icon-line" d="M18 36l-6 12M40 36l4 12M26 36l14-10"/></svg><span class="benefit-caption">Rest</span></div>
        <div class="benefit"><svg viewBox="0 0 54 54"><path class="icon-line" d="M44 20A18 18 0 0 0 12 16M10 34a18 18 0 0 0 32 4"/><path class="icon-fill" d="M30 14 20 30h7l-3 11 11-16h-7z"/></svg><span class="benefit-caption">Renew</span></div>
      </div>
      <div class="directions"><h3>Direction:</h3><p>Take 3 capsules daily, in the morning or afternoon, with or without food.</p></div>
      <div class="band-bottom"><div class="band-note"><span>Dietary supplement</span><span>Dietary supplement</span><span>Dietary supplement</span></div></div>
      <div class="servings-notch"><div class="servings-count">30</div><div class="servings-word">SERVINGS</div></div>
      <span class="band-fact band-fact--left">90 Capsules</span>
      <span class="band-fact band-fact--right">3 Per Serving</span>
    </article>
  </section>

</main>
</body>
</html>
```